Flyer Vacation Gift Certificate

I need to create a beautiful flyer 8.5 x 11 PDF format flyer design. <br/><br/>Instructions:<br/>The flyer will really be a gift voucher for a las vegas vacation getaway. So must have a Las Vegas Theme exciting fun<br/><br/>The voucher should have two modules that will be editable. <br/>Must have a "Compliments Of" area and also must have an "Exclusively For" area<br/><br/>Keep in mind that this flyer will be printed so keep that in mind :)<br/><br/>Here the is the content for the vacation voucher:<br/><br/>There is no doubt that Las Vegas is one of the hottest travel destinations around the world. In fact, some people would even go as far as<br/>saying that perhaps it is THE hottest place to visit. Enjoy up to 4 nights of resort/casino accommodations in exciting Las Vegas, NV. Millions of people travel to this exciting city each year to enjoy its thrills. Thanks to the business you received this certificate from, now you can enjoy exciting Las Vegas, NV too!<br/><br/>Features:<br/>*Travel 7 Days A Week<br/>*Stay Your Choice Of Nights (1-4 Nights)<br/>*Good For Two Adults & Two Children<br/>*Pay Just The Taxes & Fees<br/>*Multiple Travel Date Requests Allowed<br/>*Fully Transferable To Another Person<br/>*Just A 30 Days Advance Notice Required<br/>*You Will Have 12 Months To Complete Travel After Redemption<br/><br/>HOW CAN WE DO THIS?<br/><br/>We contract with the world leading hotel chains and resorts to help them fill their otherwise empty rooms.<br/><br/>We help fill empty rooms which the hotels, resorts and cruise lines turn into additional revenue from other areas of their property and future bookings.<br/><br/>Hotels rarely experience full occupancy, yet they remain open, providing rooms and services at fixed costs. So when hotels give out their rooms by partnering with marketing companies like us, they might miss out on the room fee, but they already didn't have that in the first place, at least now they have the opportunity to gain a customer for their in-house restaurants, room service, their casinos, an extra day stay, future bookings, etc.<br/><br/>VIEW ALL THE DETAILS OF THIS SPECIAL OFFER AND REDEEM ONLINE AT <br/>WWW.QOTAVERNIX.COM<br/><br/>Certificate ID # 47261-38157<br/>Expires 02/29/2020<br/><br/><br/>*terms and conditions apply see website for details<br/><br/>KEEP IN MIND THE EXAMPLES I AM UPLOADING ARE SIMPLY TO SHOW YOU THAT THEY CONTAIN THE "COMPLIMENTS OF" AND "EXCLUSIVELY FOR" ELEMENTS. THESE MUST BE INCLUDED IN NEW DESIGN. PLEASE ONLY USE THE CONTENT I PROVIDED IN BRIEF, DONT USE CONTENT FROM EXAMPLES.

Target Market(s)

CONSUMERS THAT HAVE BEEN REWARDED WITH A VACATION CERTIFICATE FOR DOING BUSINESS WITH A COMPANY.

COMPANIES USE THESE AS MARKETING INCENTIVES TO ATTRACT MORE CUSTOMERS AND TO REWARD LOYALTY, ETC.

Industry/Entity Type

Travel Industry

Colors

Designer to choose colors to be used in the design.

Requirements
Must have
• I need to create a beautiful flyer 8.5 x 11 PDF format flyer design.
• Instructions:
• The flyer will really be a gift voucher for a las vegas vacation getaway. So must have a Las Vegas Theme exciting fun
• The voucher should have two modules that will be editable.
• Must have a "Compliments Of" area and also must have an "Exclusively For" area
• Keep in mind that this flyer will be printed so keep that in mind :)
• Here the is the content for the vacation voucher:
• There is no doubt that Las Vegas is one of the hottest travel destinations around the world. In fact, some people would even go as far as
• saying that perhaps it is THE hottest place to visit. Enjoy up to 4 nights of resort/casino accommodations in exciting Las Vegas, NV. Millions of people travel to this exciting city each year to enjoy its thrills. Thanks to the business you received this certificate from, now you can enjoy exciting Las Vegas, NV too!
• Features:
• *Travel 7 Days A Week
• *Stay Your Choice Of Nights (1-4 Nights)
• *Good For Two Adults & Two Children
• *Pay Just The Taxes & Fees
• *Multiple Travel Date Requests Allowed
• *Fully Transferable To Another Person
• *Just A 30 Days Advance Notice Required
• *You Will Have 12 Months To Complete Travel After Redemption
• HOW CAN WE DO THIS?
• We contract with the world leading hotel chains and resorts to help them fill their otherwise empty rooms.
• We help fill empty rooms which the hotels, resorts and cruise lines turn into additional revenue from other areas of their property and future bookings.
• Hotels rarely experience full occupancy, yet they remain open, providing rooms and services at fixed costs. So when hotels give out their rooms by partnering with marketing companies like us, they might miss out on the room fee, but they already didn't have that in the first place, at least now they have the opportunity to gain a customer for their in-house restaurants, room service, their casinos, an extra day stay, future bookings, etc.
• VIEW ALL THE DETAILS OF THIS SPECIAL OFFER AND REDEEM ONLINE AT
• WWW.QOTAVERNIX.COM
• Certificate ID # 47261-38157
• Expires 02/29/2020
• *terms and conditions apply see website for details
• KEEP IN MIND THE EXAMPLES I AM UPLOADING ARE SIMPLY TO SHOW YOU THAT THEY CONTAIN THE "COMPLIMENTS OF" AND "EXCLUSIVELY FOR" ELEMENTS. THESE MUST BE INCLUDED IN NEW DESIGN. PLEASE ONLY USE THE CONTENT I PROVIDED IN BRIEF, DONT USE CONTENT FROM EXAMPLES.
Nice to have
• EXCITING LAS VEGAS IMAGES THAT MAKE SOMEONE WANT TO GO THERE

```html
<!DOCTYPE html>
<html lang="en">
<head>
<meta charset="utf-8">
<title>Las Vegas Vacation Getaway – Gift Voucher</title>
<link rel="stylesheet" href="https://fonts.googleapis.com/css2?family=Bebas+Neue&family=Oswald:wght@500;600&family=Open+Sans:wght@400;600;700;800&display=swap">
<style>
  :root {
    --page-bg: #d9dadc;
    --navy: #0f2f6c;
    --royal: #1f55a8;
    --red: #c8202c;
    --red-deep: #8e1119;
    --gold: #f7b544;
    --white: #ffffff;
    --panel-grey: #e8eaee;
    --ink: #1c1c22;
    --muted: #7a7d84;
    --bullet-orange: #f0a42a;
    --logo-blue: #1d4e9b;
  }
  * { margin: 0; padding: 0; box-sizing: border-box; }
  html, body { width: 994px; height: 1200px; overflow: hidden; background: var(--page-bg); }
  body { font-family: "Open Sans", Arial, sans-serif; color: var(--ink); position: relative; }

  .flyer {
    position: absolute; left: 49px; top: 20px; width: 896px; height: 1160px;
    overflow: hidden; background: var(--navy);
  }
  .hero-photo {
    position: absolute; left: 0; top: 0; width: 896px; height: 440px;
    background:
      radial-gradient(circle at 70% 30%, rgba(255,190,90,.85), rgba(255,190,90,0) 35%),
      radial-gradient(circle at 30% 40%, rgba(240,200,170,.8), rgba(240,200,170,0) 30%),
      linear-gradient(135deg, #23346b 0%, #6d3d6a 35%, #c9503e 55%, #243e7f 85%);
  }
  .body-shape { position: absolute; left: 0; top: 360px; }

  .gift-ribbon {
    position: absolute; left: -62px; top: 50px; width: 260px; height: 40px;
    background: var(--red); transform: rotate(-45deg);
    color: var(--white); font-family: "Oswald", sans-serif; font-weight: 600;
    font-size: 19px; letter-spacing: .5px; text-align: center; line-height: 40px;
    box-shadow: 0 2px 6px rgba(0,0,0,.35);
  }

  .sponsor-tag {
    position: absolute; left: 671px; top: 0; width: 210px; height: 142px;
    background: var(--white); text-align: center; padding-top: 14px;
    clip-path: polygon(0 0, 100% 0, 100% 88%, 50% 100%, 0 88%);
  }
  .sponsor-tag__title { color: var(--logo-blue); font-weight: 700; font-size: 14.5px; line-height: 17px; }
  .sponsor-tag__brand {
    margin: 6px auto 4px; display: flex; align-items: center; justify-content: center; gap: 6px;
    font-weight: 800; font-size: 15px; color: var(--logo-blue);
  }
  .sponsor-tag__brand i { width: 12px; height: 12px; background: var(--red); display: block; }
  .sponsor-tag__lines { font-size: 9.5px; line-height: 12px; color: var(--ink); }

  .snapshot {
    position: absolute; background: var(--white); padding: 9px;
    box-shadow: 0 4px 12px rgba(0,0,0,.45);
  }
  .snapshot div { width: 100%; height: 100%; }
  .snapshot--venice { left: 608px; top: 175px; width: 290px; height: 190px; transform: rotate(8deg); }
  .snapshot--venice div { background: linear-gradient(160deg, #6fa2d6, #d7b07c 55%, #2a4b6a); }
  .snapshot--casino { left: 512px; top: 325px; width: 228px; height: 185px; transform: rotate(-6deg); }
  .snapshot--casino div { background: linear-gradient(145deg, #2a1a2c, #a5523d 50%, #e3c08a 75%, #3a2a20); }

  .title { position: absolute; left: 45px; top: 440px; }
  .title__main { font-family: "Bebas Neue", sans-serif; color: var(--gold); font-size: 84px; line-height: 80px; letter-spacing: 1px; text-shadow: 0 3px 4px rgba(0,0,0,.4); }
  .title__sub { font-family: "Bebas Neue", sans-serif; color: var(--white); font-size: 50px; line-height: 48px; letter-spacing: 1px; }

  .recipient { position: absolute; left: 38px; top: 580px; color: var(--white); font-size: 19px; line-height: 31px; }
  .recipient b { font-weight: 800; }
  .intro {
    position: absolute; left: 38px; top: 650px; width: 500px; color: var(--white);
    font-size: 13.2px; line-height: 19.2px;
  }

  .features {
    position: absolute; left: 537px; top: 537px; width: 337px; height: 313px;
    background: linear-gradient(180deg, var(--red), var(--red-deep));
    border-radius: 0 0 10px 10px; padding: 10px 14px 0 14px; color: var(--white);
    box-shadow: 0 3px 8px rgba(0,0,0,.35);
  }
  .features h2 { font-family: "Oswald", sans-serif; font-weight: 600; font-size: 30px; line-height: 36px; margin-bottom: 4px; }
  .features ul { list-style: none; }
  .features li {
    display: flex; gap: 10px; font-size: 14.6px; line-height: 27.6px;
    border-bottom: 1px solid rgba(255,255,255,.22);
  }
  .features li:last-child { border-bottom: 0; }
  .features li svg { flex: none; margin-top: 8px; }

  .lower-panel { position: absolute; left: 0; top: 850px; width: 896px; height: 215px; background: var(--panel-grey); }
  .how-tab {
    position: absolute; left: 0; top: 813px; width: 360px; height: 43px;
    background: linear-gradient(90deg, var(--red-deep), var(--red));
    border-radius: 0 22px 22px 0; color: var(--white);
    font-family: "Oswald", sans-serif; font-weight: 600; font-size: 21px; line-height: 43px; padding-left: 40px;
  }
  .how-list { position: absolute; left: 38px; top: 870px; width: 840px; list-style: none; }
  .how-list li { display: flex; gap: 14px; font-size: 13.2px; line-height: 19.3px; margin-bottom: 8px; }
  .how-list li svg { flex: none; margin-top: 3px; }

  .cert-meta { position: absolute; left: 0; top: 1040px; width: 896px; text-align: center; color: var(--muted); font-size: 11.5px; }

  .redeem-bar {
    position: absolute; left: 38px; top: 1067px; width: 833px; height: 44px;
    background: linear-gradient(90deg, var(--red-deep), var(--red) 50%, var(--red-deep));
    border-radius: 22px; color: var(--white); font-weight: 700; font-size: 15.5px;
    display: flex; align-items: center; justify-content: center; gap: 10px;
  }
  .terms { position: absolute; left: 0; top: 1127px; width: 896px; text-align: center; color: var(--white); font-size: 12.5px; }
</style>
</head>
<body>
<main class="flyer">
  <div class="hero-photo" role="img" aria-label="Smiling couple in front of the Welcome to Las Vegas sign at night"></div>

  <svg class="body-shape" width="896" height="800" viewBox="0 0 896 800" aria-hidden="true">
    <defs>
      <linearGradient id="bodyBlue" x1="0" y1="0" x2="0" y2="1">
        <stop offset="0" stop-color="#1f55a8"/>
        <stop offset="1" stop-color="#0d2a63"/>
      </linearGradient>
    </defs>
    <path d="M0 70 Q260 -10 560 20 L896 60 L896 800 L0 800 Z" fill="url(#bodyBlue)"/>
    <path d="M0 60 Q260 -20 560 10" fill="none" stroke="#ffffff" stroke-width="12"/>
    <path d="M0 75 Q260 0 560 28" fill="none" stroke="#c8202c" stroke-width="4"/>
  </svg>

  <div class="gift-ribbon">GIFT VOUCHER</div>

  <aside class="sponsor-tag">
    <p class="sponsor-tag__title">THIS CERTIFICATE IS<br>COMPLIMENTS OF</p>
    <p class="sponsor-tag__brand"><i></i>Textlane Hub</p>
    <p class="sponsor-tag__lines">Certificate Courtesy Of<br>Text Line 2<br>Text Line 3</p>
  </aside>

  <figure class="snapshot snapshot--venice"><div role="img" aria-label="Gondola ride along a canal at a Las Vegas resort"></div></figure>
  <figure class="snapshot snapshot--casino"><div role="img" aria-label="Friends celebrating at a casino roulette table"></div></figure>

  <header class="title">
    <h1 class="title__main">LAS VEGAS</h1>
    <p class="title__sub">VACATION GETAWAY</p>
  </header>

  <div class="recipient">
    <p><b>COMPLIMENTS OF:</b> Two Adults &amp; Two Children</p>
    <p><b>EXCLUSIVELY FOR:</b> Customer Name</p>
  </div>

  <p class="intro">There is no doubt that Las Vegas is one of the hottest travel destinations around the world. In fact, some people would even go as far as saying that perhaps it is THE hottest place to visit. Enjoy up to 4 nights of resort/casino accommodations in exciting Las Vegas, NV. Millions of people travel to this exciting city each year to enjoy its thrills. Thanks to the business you received this certificate from, now you can enjoy exciting Las Vegas, NV too!</p>

  <section class="features">
    <h2>FEATURES:</h2>
    <ul>
      <li><svg width="13" height="13" viewBox="0 0 13 13"><circle cx="6.5" cy="6.5" r="6.5" fill="#fff"/><path d="M5 3.5 L8 6.5 L5 9.5" fill="none" stroke="#c8202c" stroke-width="1.8"/></svg>Travel 7 Days A Week</li>
      <li><svg width="13" height="13" viewBox="0 0 13 13"><circle cx="6.5" cy="6.5" r="6.5" fill="#fff"/><path d="M5 3.5 L8 6.5 L5 9.5" fill="none" stroke="#c8202c" stroke-width="1.8"/></svg>Stay Your Choice Of Nights (1- 4 Nights)</li>
      <li><svg width="13" height="13" viewBox="0 0 13 13"><circle cx="6.5" cy="6.5" r="6.5" fill="#fff"/><path d="M5 3.5 L8 6.5 L5 9.5" fill="none" stroke="#c8202c" stroke-width="1.8"/></svg>Good For Two Adults &amp; Two Children</li>
      <li><svg width="13" height="13" viewBox="0 0 13 13"><circle cx="6.5" cy="6.5" r="6.5" fill="#fff"/><path d="M5 3.5 L8 6.5 L5 9.5" fill="none" stroke="#c8202c" stroke-width="1.8"/></svg>Pay Just The Taxes &amp; Fees</li>
      <li><svg width="13" height="13" viewBox="0 0 13 13"><circle cx="6.5" cy="6.5" r="6.5" fill="#fff"/><path d="M5 3.5 L8 6.5 L5 9.5" fill="none" stroke="#c8202c" stroke-width="1.8"/></svg>Multiple Travel Date Requests Allowed</li>
      <li><svg width="13" height="13" viewBox="0 0 13 13"><circle cx="6.5" cy="6.5" r="6.5" fill="#fff"/><path d="M5 3.5 L8 6.5 L5 9.5" fill="none" stroke="#c8202c" stroke-width="1.8"/></svg>Fully Transferable To Another Person</li>
      <li><svg width="13" height="13" viewBox="0 0 13 13"><circle cx="6.5" cy="6.5" r="6.5" fill="#fff"/><path d="M5 3.5 L8 6.5 L5 9.5" fill="none" stroke="#c8202c" stroke-width="1.8"/></svg>Just A 30 Days Advance Notice Required</li>
      <li><svg width="13" height="13" viewBox="0 0 13 13"><circle cx="6.5" cy="6.5" r="6.5" fill="#fff"/><path d="M5 3.5 L8 6.5 L5 9.5" fill="none" stroke="#c8202c" stroke-width="1.8"/></svg>You Will Have 12 Months To Complete<br>Travel After Redemption</li>
    </ul>
  </section>

  <div class="lower-panel"></div>
  <h2 class="how-tab">HOW CAN WE DO THIS?</h2>
  <ul class="how-list">
    <li><svg width="14" height="14" viewBox="0 0 14 14"><circle cx="7" cy="7" r="6" fill="none" stroke="#f0a42a" stroke-width="1.5"/><path d="M5.5 4 L8.5 7 L5.5 10" fill="none" stroke="#f0a42a" stroke-width="1.6"/></svg><span>We contract with the world leading hotel chains and resorts to help them fill their otherwise empty rooms.</span></li>
    <li><svg width="14" height="14" viewBox="0 0 14 14"><circle cx="7" cy="7" r="6" fill="none" stroke="#f0a42a" stroke-width="1.5"/><path d="M5.5 4 L8.5 7 L5.5 10" fill="none" stroke="#f0a42a" stroke-width="1.6"/></svg><span>We help fill empty rooms which the hotels, resorts and cruise lines turn into additional revenue from other areas of their property and future bookings.</span></li>
    <li><svg width="14" height="14" viewBox="0 0 14 14"><circle cx="7" cy="7" r="6" fill="none" stroke="#f0a42a" stroke-width="1.5"/><path d="M5.5 4 L8.5 7 L5.5 10" fill="none" stroke="#f0a42a" stroke-width="1.6"/></svg><span>Hotels rarely experience full occupancy, yet they remain open, providing rooms and services at fixed costs. So when hotels give out their rooms by partnering with marketing companies like us, they might miss out on the room fee, but they already didn't have that in the first place, at least now they have the opportunity to gain a customer for their in-house restaurants, room service, their casinos, an extra day stay, future bookings, etc.</span></li>
  </ul>

  <p class="cert-meta">Certificate ID # 47261-38157 &nbsp;|&nbsp; Expires 02/29/2020</p>

  <div class="redeem-bar">
    <span>VIEW ALL THE DETAILS OF THIS SPECIAL OFFER AND REDEEM ONLINE AT</span>
    <svg width="14" height="14" viewBox="0 0 14 14" aria-hidden="true"><circle cx="7" cy="7" r="6" fill="none" stroke="#fff" stroke-width="1.3"/><ellipse cx="7" cy="7" rx="2.6" ry="6" fill="none" stroke="#fff" stroke-width="1.1"/><path d="M1 7 H13" stroke="#fff" stroke-width="1.1"/></svg>
    <span>WWW.QOTAVERNIX.COM</span>
  </div>

  <p class="terms">*terms and conditions apply see website for details</p>
</main>
</body>
</html>
```